Sell the dream! Property investment proposal document

We are looking for a proposal document which outlines our vision for property development. The purpose of the document is to raise investment from investors - sell the dream!
Brief summary:
Kestrel Dwellings Developments, is an emerging New Zealand property investment company with a focus on providing unique property investment opportunities.
Our expertise and capabilities in architectural modular homes provide us with a remarkable advantage in tackling the development of properties that are typically considered challenging, remote, or uniquely positioned.
Our specialization in this niche sector of property development not only sets us apart from competitors, but also paves the way for lucrative investment opportunities in the New Zealand property market.
Feel free to use any images from www.kestreldwellings.co.nz
Target Market(s)
investors for a unique property development opportunity
Industry/Entity Type
luxury property development in unique locations throughout New Zealand
Colors
Designer to choose only greyscale colors for use in the design.
Look and feel

```html
<!DOCTYPE html>
<html lang="en">
<head>
<meta charset="utf-8">
<title>Kestrel Dwellings — Sell the dream!</title>
<link href="https://fonts.googleapis.com/css2?family=Inter+Tight:wght@300;400;700&display=swap" rel="stylesheet">
<style>
  :root {
    --bg: #2e2d2e;
    --ink: #ffffff;
    --muted: #8c8c8c;
    --frame: #d9d9d9;
  }
  * { margin: 0; padding: 0; box-sizing: border-box; }
  html, body { width: 1200px; height: 846px; overflow: hidden; background: var(--bg); }
  body { position: relative; font-family: "Inter Tight", "Helvetica Neue", Arial, sans-serif; color: var(--ink); font-weight: 300; }
  .abs { position: absolute; }

  .tagline { left: 45px; top: 78px; width: 540px; font-size: 23px; line-height: 26.5px; font-weight: 300; letter-spacing: -0.3px; }
  .tagline strong { font-weight: 700; }

  .heading { font-size: 23px; font-weight: 700; letter-spacing: -0.2px; line-height: 26px; }
  .about-heading { left: 654px; top: 43px; }
  .approach-heading { left: 46px; top: 443px; }

  .body-copy { font-size: 16.6px; letter-spacing: -0.2px; }
  .about-copy { left: 654px; top: 85px; width: 520px; line-height: 20.6px; }
  .about-copy p { margin-bottom: 18px; }
  .approach-copy { left: 46px; top: 485px; width: 520px; line-height: 19px; }
  .approach-copy p { margin-bottom: 17px; }

  .photo { border: 1px solid var(--frame); }
  .photo-hero { left: -1px; top: 159px; width: 585px; height: 246px;
    background: linear-gradient(180deg, #aeb9c2 0%, #cfd3d6 38%, #2a2a2a 48%, #3a3a3a 66%, #5e6a4a 80%, #4f5b3c 100%); }
  .photo-living { left: 766px; top: 329px; width: 426px; height: 213px; z-index: 2;
    background: linear-gradient(180deg, #5a4d43 0%, #c9ccd0 25%, #b9bec4 55%, #a89c8f 72%, #6f6559 100%); }
  .photo-bath { left: 631px; top: 473px; width: 242px; height: 311px; z-index: 1;
    background: linear-gradient(180deg, #bdbcba 0%, #8e9a7a 35%, #cfcdca 60%, #7d7a76 100%); }

  .caption { font-size: 10.5px; font-weight: 400; letter-spacing: 0.3px; text-align: right; white-space: nowrap; }
  .caption-hero { right: 615px; top: 411px; }
  .caption-living { right: 8px; top: 549px; }
  .caption-bath { right: 327px; top: 790px; }

  .wordmark { right: 32px; top: 740px; font-size: 36px; font-weight: 300; letter-spacing: 1px; line-height: 40px; color: var(--ink); }

  .folio { top: 817px; font-size: 12px; font-weight: 300; color: var(--muted); }
  .folio-num { color: var(--ink); border-bottom: 1px solid var(--ink); padding-bottom: 1px; }
  .folio-left-num { left: 19px; }
  .folio-left-name { left: 46px; }
  .folio-right-name { right: 32px; }
  .folio-right-num { right: 7px; }
</style>
</head>
<body>
  <h1 class="abs tagline"><strong>Kestrel:</strong> Modular, architectural homes with flexibility and sophistication.</h1>

  <div class="abs photo photo-hero" role="img" aria-label="Dusk render of a long dark-clad single-storey home with lit windows, terrace and lawn"></div>
  <div class="abs caption caption-hero">The Atelier Range No. 1</div>

  <h2 class="abs heading approach-heading">Our unique approach</h2>
  <div class="abs body-copy approach-copy">
    <p>Architecturally-designed, highly customisable homes, built off-site, delivered to and assembled on a plot of land anywhere in New Zealand.</p>
    <p>At Kestrel, our aim is to help people envision their own homes; to simplify the process of crafting and building them to exacting standards; and give our customers and their families personalised homes in which to forge memories of shelter and comfort.</p>
    <p>Our manufacturing processes have been tried, perfected and are independent of weather or site constraints, allowing for a regimented building phase and fast turnaround times.</p>
    <p>By delivering prefabricated and ready-to-assemble components to your site, we minimise the number of workers, tools, vehicles and time required on site.</p>
  </div>

  <h2 class="abs heading about-heading">About us</h2>
  <div class="abs body-copy about-copy">
    <p>Kestrel Dwellings Developments is an emerging New Zealand property investment company with a focus on providing unique property investment opportunities.</p>
    <p>Our expertise and capabilities in architectural modular homes provide us with a remarkable advantage in tackling the development of properties that are typically considered challenging, remote, or uniquely positioned.</p>
    <p>Our specialization in this niche sector of property development not only sets us apart from the competition, but paves the way for lucrative investment opportunities in the New Zealand property market.</p>
  </div>

  <div class="abs photo photo-living" role="img" aria-label="Interior render of a living room with timber walls, pale sofa and a wide window onto the sea"></div>
  <div class="abs caption caption-living">The Atelier Range No. 2</div>

  <div class="abs photo photo-bath" role="img" aria-label="Interior render of a concrete-walled bathroom with freestanding bath and a window onto greenery"></div>
  <div class="abs caption caption-bath">Tranquil Haven</div>

  <div class="abs wordmark">Kestrel</div>

  <span class="abs folio folio-num folio-left-num">2</span>
  <span class="abs folio folio-left-name">Kestrel Dwellings</span>
  <span class="abs folio folio-right-name">Sell the dream!</span>
  <span class="abs folio folio-num folio-right-num">3</span>
</body>
</html>
```